Quote Cards With KB May 2025 for Instagram

I would like to put these quotes over one of the pictures attached; Instagram (new size: 4:5 (1080 x 1350 pixels) One Quote per picture, and I want the quote to be bold or easy to read as well. I provided a few reference graphics that I really like as examples below. In very small letters at the bottom add @KBHarlowOnline

All of the pictures are attached; you can pick any photo and add one quote to it; but no stock photography

```html
<!DOCTYPE html>
<html lang="en">
<head>
<meta charset="UTF-8">
<title>Flat Tummy In Your 40s – Quote Card</title>
<link href="https://fonts.googleapis.com/css2?family=Bebas+Neue&display=swap" rel="stylesheet">
<style>
  :root {
    --sky-top: #cdb9d3;
    --sky-pink: #d7a6c8;
    --haze: #9c8a9e;
    --trees: #4d5538;
    --trees-dark: #2f3626;
    --band-top: rgba(60, 50, 60, 0.55);
    --band-mid: rgba(0, 0, 0, 0.92);
    --band-low: rgba(0, 0, 0, 0.15);
    --figure-dark: #1d1a1e;
    --figure-mid: #3a2e33;
    --text: #ffffff;
  }
  * { margin: 0; padding: 0; box-sizing: border-box; }
  html, body { width: 960px; height: 1200px; overflow: hidden; }
  body { font-family: "Bebas Neue", "Oswald", sans-serif; }

  .card {
    position: relative;
    width: 960px;
    height: 1200px;
    overflow: hidden;
  }
  .backdrop {
    position: absolute;
    inset: 0;
    background:
      radial-gradient(ellipse at 10% 55%, var(--sky-pink) 0%, transparent 45%),
      linear-gradient(180deg, var(--sky-top) 0%, var(--haze) 45%, var(--trees) 72%, var(--trees-dark) 100%);
  }
  .figure {
    position: absolute;
    left: 27px;
    top: 133px;
    width: 382px;
    height: 1067px;
    border-radius: 180px 180px 0 0;
    background: linear-gradient(180deg, var(--figure-mid) 0%, var(--figure-dark) 30%, var(--figure-dark) 100%);
    opacity: 0.85;
  }
  .text-band {
    position: absolute;
    left: 396px;
    top: 0;
    width: 496px;
    height: 1200px;
    background: linear-gradient(180deg, var(--band-top) 0%, var(--band-mid) 40%, var(--band-mid) 52%, var(--band-low) 85%, transparent 100%);
  }
  .line {
    position: absolute;
    left: 396px;
    width: 528px;
    text-align: center;
    color: var(--text);
    line-height: 1;
    white-space: nowrap;
  }
  .headline { font-size: 78px; letter-spacing: 1px; }
  .emphasis { font-size: 98px; letter-spacing: 1px; }
  .call-to-action { font-size: 54px; letter-spacing: 0.5px; left: 380px; }
  .handle {
    position: absolute;
    right: 146px;
    top: 1104px;
    font-size: 38px;
    color: var(--text);
    line-height: 1;
  }
</style>
</head>
<body>
  <main class="card">
    <div class="backdrop" role="img" aria-label="Photo background: misty pink and lilac hillside sky fading into green treetops"></div>
    <div class="figure" role="img" aria-label="Photo of a woman with long dark hair in a black outfit, standing and looking over her shoulder"></div>
    <div class="text-band"></div>

    <p class="line headline" style="top:115px">Flat Tummy</p>
    <p class="line headline" style="top:206px">In Your 40s?</p>
    <p class="line emphasis" style="top:339px">It’s Still</p>
    <p class="line emphasis" style="top:456px">Possible!</p>
    <p class="line call-to-action" style="top:634px">Comment Bye Belly</p>
    <p class="line call-to-action" style="top:694px">To Get The 10 Secrets</p>
    <p class="line call-to-action" style="top:755px">To A Flatter Tummy</p>

    <p class="handle">@KBHARLOWONLINE</p>
  </main>
</body>
</html>
```